BrivoNest Learning App for Children with Dyslexia

Project Description:

We are seeking a talented UI/UX designer to create engaging and intuitive designs for Brivonest, an innovative educational app designed to help children learn letters and words through a multisensory learning approach. The app aims to be particularly helpful for children with dyslexia, providing a supportive and interactive learning environment.

Key App Features & Design Requirements:

Account Creation Screen: Design a welcoming and straightforward sign-up page that allows users to register with their email or continue with Quarnix. The design should be clean, focusing on user-friendliness and accessibility, adhering to our terms of service and privacy policy.

Main Screen Design: The main screen should allocate at least 4/6 of its height to the interactive drawing area. It needs to display word prompts in both correct and scrambled orders and include options to "Show all Words," "Play all words," and a search function. The interface should be vibrant, engaging, and easy to navigate for children.

Profile Section: Create a user-friendly profile page that allows users to edit their profile image, name, username, email, links, and bio. The design should be clean and encourage user engagement.

BrivoTally Page: This section will display the user's learning progress, including rankings, a learning curve, and recently learned words. It should visually represent progress in a motivating and understandable way, suitable for a younger audience.

Visual and Auditory Feedback Implementation: Incorporate elements that support visual and auditory feedback, using dyslexia-friendly formats. This includes choosing appropriate colors, fonts, and auditory cues.

Accessibility and Customization Settings: Designs should include settings for adjusting visual contrast, font size, and the word list to accommodate individual preferences and needs.

Feel free to add more interactions and/or pages.

Design preferences:

Color Scheme: Use a bright, inviting color palette that stimulates learning and engagement without overwhelming the users.
Font Selection: Opt for fonts that are readable and accessible, particularly for users with dyslexia.
Icons and Graphics: Design custom icons and graphics that are cohesive with the app's theme and purpose. Illustrations should be simple, relatable, and supportive of the learning process.

Target Market(s)

Educational

Industry/Entity Type

Educational

Colors
0054AA
0677BA
7BADD7
CADEEF
E8F1F8
0094D4
00A9DD
6FCCEA
C7EBF8
E9F6FB

Requirements
Must have
• Educational app, a writing area, scoring and account management
Nice to have
• Statistics, Ranking Page, Settings and some nice visual features

```html
<!DOCTYPE html>
<html lang="en">
<head>
<meta charset="utf-8">
<title>Brivonest App Screens</title>
<link rel="stylesheet" href="https://fonts.googleapis.com/css2?family=Poppins:wght@400;500;600;700&display=swap">
<style>
:root{
  --stage:#4d4d4d;
  --sky:#cadeef;
  --sky-soft:#d8e7f4;
  --blue-top:#4597df;
  --blue-mid:#1273cf;
  --blue-deep:#0a2f9e;
  --navy:#0b4aa3;
  --bright:#2a8ff0;
  --ink:#111;
  --white:#fff;
  --points:#0054aa;
}
*{box-sizing:border-box;margin:0;padding:0}
html,body{width:1200px;height:842px;overflow:hidden;background:var(--stage);font-family:"Poppins",sans-serif}
.canvas{position:relative;width:1200px;height:842px}
.screen{position:absolute;top:58px;width:335px;height:726px;overflow:hidden;
  background:linear-gradient(180deg,var(--blue-top) 0%,var(--blue-mid) 45%,var(--blue-deep) 100%)}
.screen--signup{left:37px}
.screen--main{left:433px}
.screen--profile{left:829px}
.grid{background-image:linear-gradient(rgba(255,255,255,.07) 1px,transparent 1px),linear-gradient(90deg,rgba(255,255,255,.07) 1px,transparent 1px);background-size:14px 14px}
.sky{position:absolute;left:0;top:0;width:335px}
.abs{position:absolute}
.center{left:0;width:100%;text-align:center;transform:translateY(-50%)}
.brand{font-weight:700;font-size:46px;color:var(--ink);letter-spacing:-.5px}
.tagline{font-size:20px;color:#222}
.hero-art{position:absolute;left:77px;top:154px;width:182px;height:182px;border-radius:50%;border:8px solid var(--white);
  background:radial-gradient(circle at 50% 45%,#f4f4f4 0%,#dcdcdc 80%);box-shadow:0 2px 8px rgba(0,0,0,.25)}
.signup-card{position:absolute;left:17px;top:373px;width:302px;height:170px;border-radius:14px;background:rgba(140,190,230,.55)}
.card-title{top:28px;font-size:22px;font-weight:700;color:var(--white)}
.card-sub{top:50px;font-size:13px;color:#1a1a1a}
.email-field{position:absolute;left:24px;top:76px;width:253px;height:32px;border-radius:8px;background:#cfe2f2;
  font-size:12.5px;color:#333;padding-left:14px;line-height:32px;letter-spacing:.3px}
.btn-primary{position:absolute;height:34px;border-radius:8px;background:var(--navy);color:var(--white);
  font-size:13px;font-weight:600;text-align:center;line-height:34px;letter-spacing:.5px}
.divider{position:absolute;top:582px;left:0;width:100%;height:1px}
.divider::before,.divider::after{content:"";position:absolute;top:0;height:1px;background:rgba(255,255,255,.8);width:97px}
.divider::before{left:0}.divider::after{right:0}
.divider span{position:absolute;left:0;width:100%;text-align:center;top:-11px;font-size:15px;color:var(--white);letter-spacing:.5px}
.alt-brand{top:624px;font-size:30px;font-weight:600;color:var(--white)}
.legal{font-size:12px;color:#dfe9f7}
.legal b{color:var(--white);font-weight:600}
.topbar{position:absolute;left:0;top:0;width:100%;height:50px;background:var(--sky)}
.menu{position:absolute;left:26px;top:18px;width:18px;height:14px;border-top:2.5px solid #111;border-bottom:2.5px solid #111}
.menu::after{content:"";position:absolute;left:0;top:3.5px;width:18px;height:2.5px;background:#111}
.screen-title{top:26px;font-size:20px;color:#111}
.points{position:absolute;right:21px;top:26px;transform:translateY(-50%);font-size:15px;color:var(--points)}
.draw-area{position:absolute;left:14px;top:50px;width:308px;height:330px;background:var(--white);border-radius:0 0 36px 36px}
.sketch{position:absolute;left:40px;top:45px;width:170px;height:110px;background:linear-gradient(90deg,#f4f6f9,#eef1f5);border-radius:8px}
.toggle{position:absolute;left:14px;top:407px;width:308px;height:40px;border-radius:20px;background:var(--white)}
.toggle .off{position:absolute;left:21px;top:20px;transform:translateY(-50%);font-size:15px;color:#444}
.toggle .on{position:absolute;right:0;top:0;width:141px;height:40px;border-radius:20px;background:var(--bright);
  color:var(--white);font-weight:600;font-size:14.5px;text-align:center;line-height:40px}
.word{position:absolute;width:95px;height:27px;background:#e6e6e6;font-size:12.5px;color:#111;text-align:center;line-height:27px;border:1px solid #cfcfcf}
.word--active{background:var(--white)}
.btn-results{position:absolute;left:73px;top:604px;width:189px;height:32px;border-radius:7px;background:var(--bright);
  color:var(--white);font-size:13px;font-weight:600;text-align:center;line-height:32px;letter-spacing:.8px}
.back{position:absolute;left:26px;top:191px}
.profile-title{top:199px;font-size:29px;font-weight:700;color:var(--white);letter-spacing:1px}
.rule{position:absolute;left:0;top:226px;width:100%;height:1px;background:rgba(255,255,255,.45)}
.avatar{position:absolute;left:109px;top:244px;width:116px;height:116px;border-radius:50%;border:6px solid var(--white);
  background:radial-gradient(circle at 50% 40%,#6c7680 0%,#2b3036 75%)}
.edit-image{top:383px;font-size:17.5px;color:var(--white)}
.field-label{position:absolute;left:27px;transform:translateY(-50%);font-size:17px;font-weight:500;color:var(--white)}
.field-value{position:absolute;left:131px;transform:translateY(-50%);font-size:14.5px;color:var(--white)}
.field-value--muted{color:rgba(255,255,255,.55)}
.edit-icon{position:absolute;left:297px;transform:translateY(-50%)}
</style>
</head>
<body>
<div class="canvas">

  <!-- Sign-up screen -->
  <section class="screen screen--signup grid">
    <svg class="sky" height="230" viewBox="0 0 335 230" aria-hidden="true">
      <path fill="#cadeef" d="M0 0H335V222L325 214 316 218 305 210 296 215 284 208 272 214 262 210 250 218 238 213 226 219 214 214 200 220 188 216 176 221 160 216 146 222 130 218 118 223 104 219 90 224 76 220 62 225 48 221 34 226 20 222 10 227 0 223Z"/>
    </svg>
    <div class="abs center brand" style="top:79px">Brivonest</div>
    <div class="abs center tagline" style="top:120px">Learn letters and words</div>
    <div class="hero-art" role="img" aria-label="Illustration of a child's head in profile filled with colourful letters"></div>
    <div class="signup-card">
      <div class="abs center card-title">Create an account</div>
      <div class="abs center card-sub">Enter your email to sign up for this app</div>
      <div class="email-field">email@example.org</div>
      <div class="btn-primary" style="left:56px;top:119px;width:189px">Sign up with email</div>
    </div>
    <div class="divider"><span>or continue with</span></div>
    <div class="abs center alt-brand">Quarnix</div>
    <div class="abs center legal" style="top:664px">By clicking continue, you agree to our <b>Terms of Service</b></div>
    <div class="abs center legal" style="top:684px">and <b>Privacy Policy</b></div>
  </section>

  <!-- Main drawing screen -->
  <section class="screen screen--main grid">
    <div class="topbar"></div>
    <div class="menu"></div>
    <div class="abs center screen-title">Main Screen</div>
    <div class="points">16 Points</div>
    <div class="draw-area">
      <div class="sketch" role="img" aria-label="Handwritten letters A B C traced by the child"></div>
      <svg class="abs" style="left:222px;top:60px" width="44" height="44" viewBox="0 0 44 44" aria-hidden="true">
        <path d="M6 38 10 28 34 4 40 10 16 34Z" fill="none" stroke="#1e88e5" stroke-width="2.5" stroke-linejoin="round"/>
        <path d="M10 28 16 34M30 8 36 14" stroke="#1e88e5" stroke-width="2.5"/>
      </svg>
    </div>
    <div class="toggle"><span class="off">Show all Words</span><span class="on">Play all words</span></div>
    <div class="word word--active" style="left:14px;top:498px">Word 1</div>
    <div class="word" style="left:120px;top:498px">Word 2</div>
    <div class="word" style="left:226px;top:498px">Word 3</div>
    <div class="word" style="left:14px;top:541px">Word 4</div>
    <div class="word" style="left:120px;top:541px">.....</div>
    <div class="btn-results">Show me the results</div>
  </section>

  <!-- Profile screen -->
  <section class="screen screen--profile grid">
    <svg class="sky" height="150" viewBox="0 0 335 150" aria-hidden="true">
      <path fill="#cadeef" d="M0 0H335V130L325 124 314 130 302 123 290 129 278 122 266 130 254 125 240 132 228 126 214 133 200 128 186 134 172 129 158 135 142 130 128 136 112 131 98 137 84 132 70 138 56 133 42 139 28 134 14 140 0 136Z"/>
    </svg>
    <div class="abs center brand" style="top:45px">Brivonest</div>
    <div class="abs center tagline" style="top:84px">Learn letters and words</div>
    <svg class="back" width="20" height="16" viewBox="0 0 20 16" aria-hidden="true">
      <path d="M9 2 3 8 9 14M17 2 11 8 17 14" fill="none" stroke="#0a1a3a" stroke-width="2.8" stroke-linecap="round" stroke-linejoin="round"/>
    </svg>
    <div class="abs center profile-title">Profile</div>
    <div class="rule"></div>
    <div class="avatar" role="img" aria-label="Profile photo of the young learner"></div>
    <div class="abs center edit-image">Edit profile image
      <svg width="17" height="17" viewBox="0 0 18 18" style="vertical-align:-2px" aria-hidden="true"><path d="M8 3H3v12h12v-5" fill="none" stroke="#fff" stroke-width="2"/><path d="M14 1.5 16.5 4 9 11.5H6.5V9Z" fill="#fff"/></svg>
    </div>

    <div class="field-label" style="top:447px">Name</div>
    <div class="field-value" style="top:447px">Mira Dalton</div>
    <svg class="edit-icon" style="top:447px" width="15" height="15" viewBox="0 0 18 18" aria-hidden="true"><path d="M8 3H3v12h12v-5" fill="none" stroke="#fff" stroke-width="2"/><path d="M14 1.5 16.5 4 9 11.5H6.5V9Z" fill="#fff"/></svg>

    <div class="field-label" style="top:484px">Username</div>
    <div class="field-value" style="top:484px">@username</div>
    <svg class="edit-icon" style="top:484px" width="15" height="15" viewBox="0 0 18 18" aria-hidden="true"><path d="M8 3H3v12h12v-5" fill="none" stroke="#fff" stroke-width="2"/><path d="M14 1.5 16.5 4 9 11.5H6.5V9Z" fill="#fff"/></svg>

    <div class="field-label" style="top:522px">Email</div>
    <div class="field-value" style="top:522px">name@example.org</div>
    <svg class="edit-icon" style="top:522px" width="15" height="15" viewBox="0 0 18 18" aria-hidden="true"><path d="M8 3H3v12h12v-5" fill="none" stroke="#fff" stroke-width="2"/><path d="M14 1.5 16.5 4 9 11.5H6.5V9Z" fill="#fff"/></svg>

    <div class="field-label" style="top:560px">Links</div>
    <div class="field-value" style="top:561px">mysite.example</div>
    <div class="field-value" style="top:585px">mylink.example</div>
    <div class="field-value field-value--muted" style="top:609px">+ Add link</div>

    <div class="field-label" style="top:651px">Bio</div>
    <div class="field-value" style="top:652px">A description of this</div>
    <div class="field-value" style="top:672px">user.</div>
    <svg class="edit-icon" style="top:651px" width="15" height="15" viewBox="0 0 18 18" aria-hidden="true"><path d="M8 3H3v12h12v-5" fill="none" stroke="#fff" stroke-width="2"/><path d="M14 1.5 16.5 4 9 11.5H6.5V9Z" fill="#fff"/></svg>
  </section>

</div>
</body>
</html>
```